Meadowlark Property Review is a leading provider of residential appraisal and home inspection products in S

I need a business card/logo designed that obviously describes my business. We are a residential appraisal and home inspection company in Springfield, MO. We offer residential appraisals, home inspection, pest inspection and radon gas measurement. We have been in business for 18 years and hold state certified residential appraisal licenses and OBREX certified home inspection licenses. I have a logo that I really like and will attach, but would be open to new suggestions. I like more modern designs than traditional and would like a two sided card with our services, licenses and qualifications on the back.

```html
<!DOCTYPE html>
<html lang="en">
<head>
<meta charset="utf-8">
<title>Meadowlark Property Review – Business Card</title>
<link rel="stylesheet" href="https://fonts.googleapis.com/css2?family=Source+Sans+3:ital,wght@0,400;0,600;0,700;1,400&display=swap">
<style>
  :root {
    --backdrop: #3d3d3d;
    --paper: #f7f7f7;
    --earth: #8c6a40;
    --amber: #ef8a1d;
    --ink-light: #ffffff;
  }
  * { margin: 0; padding: 0; box-sizing: border-box; }
  html, body {
    width: 1200px; height: 750px; overflow: hidden;
    background: var(--backdrop);
    font-family: "Source Sans 3", "Myriad Pro", sans-serif;
  }
  .canvas { position: relative; width: 1200px; height: 750px; }

  .card {
    position: absolute; top: 228px;
    width: 462px; height: 262px; overflow: hidden;
  }
  .card--front { left: 124px; background: var(--paper); }
  .card--back { left: 618px; background: var(--amber); }

  /* Front */
  .front-band { position: absolute; inset: 0; }
  .wordmark {
    position: absolute; left: 0; right: 0; top: 76px;
    display: flex; justify-content: center; align-items: center; gap: 10px;
  }
  .wordmark__square { width: 14px; height: 14px; background: var(--amber); }
  .wordmark__name {
    font-weight: 700; font-size: 24px; color: var(--earth); letter-spacing: -0.2px;
  }

  .identity {
    position: absolute; right: 258px; top: 172px;
    text-align: right; color: var(--ink-light);
    font-size: 11.5px; line-height: 17px;
  }
  .identity__name { font-size: 16.5px; font-weight: 600; color: var(--amber); line-height: 20px; }
  .identity__role { font-size: 12.5px; margin-bottom: 1px; }

  .divider {
    position: absolute; left: 222px; top: 177px;
    width: 1px; height: 70px; background: rgba(255,255,255,0.7);
  }

  .contacts {
    position: absolute; left: 240px; top: 174px;
    list-style: none; color: var(--ink-light); font-size: 11.5px;
  }
  .contacts li { display: flex; align-items: center; gap: 6px; height: 17.6px; }
  .contacts svg { width: 12px; height: 12px; fill: var(--amber); flex: none; }

  /* Back */
  .back-name {
    position: absolute; left: 0; right: 0; top: 110px;
    display: flex; justify-content: center; align-items: center; gap: 10px;
  }
  .back-name__square { width: 16px; height: 16px; background: var(--ink-light); }
  .back-name__text { font-weight: 700; font-size: 26px; color: var(--ink-light); }
  .services {
    position: absolute; left: 0; right: 0; top: 198px;
    text-align: center; font-style: italic; color: var(--ink-light);
    font-size: 12.5px; line-height: 18px;
  }
</style>
</head>
<body>
<main class="canvas">

  <section class="card card--front" aria-label="Card front">
    <svg class="front-band" viewBox="0 0 462 262" width="462" height="262" aria-hidden="true">
      <path d="M0,166 Q231,142 462,166 L462,262 L0,262 Z" fill="var(--earth)"/>
      <path d="M30,160 Q231,128 432,160 Q231,136 30,160 Z" fill="var(--amber)"/>
    </svg>

    <div class="wordmark">
      <span class="wordmark__square"></span>
      <span class="wordmark__name">Meadowlark Property Review</span>
    </div>

    <div class="identity">
      <p class="identity__name">Avery Lindqvist</p>
      <p class="identity__role">CEO/Founder</p>
      <p>2140 Harlow Court</p>
      <p>Springfield, Missouri 65804</p>
    </div>

    <div class="divider"></div>

    <ul class="contacts">
      <li>
        <svg viewBox="0 0 12 12" aria-label="Phone"><path d="M2.3 0.8 L4.2 0.5 L5 3 L3.7 4 Q4.6 6.5 7.5 8 L8.6 6.8 L11.2 7.6 L11 9.6 Q10.3 11.2 8.5 11 Q2 9.5 1 3 Q1 1.3 2.3 0.8 Z"/></svg>
        417 555 0182
      </li>
      <li>
        <svg viewBox="0 0 12 12" aria-label="Fax"><rect x="3" y="0.5" width="6" height="3.5"/><rect x="0.5" y="4.5" width="11" height="5" rx="1"/><rect x="3" y="8" width="6" height="3.5" fill="var(--earth)" stroke="var(--amber)" stroke-width="1"/></svg>
        417 555 0194
      </li>
      <li>
        <svg viewBox="0 0 12 12" aria-label="Email"><rect x="0.5" y="2" width="11" height="8"/><path d="M0.5 2 L6 6.5 L11.5 2" fill="none" stroke="var(--earth)" stroke-width="1"/></svg>
        hello@meadowlarkreview.com
      </li>
      <li>
        <svg viewBox="0 0 12 12" aria-label="Website"><circle cx="6" cy="6" r="5.5"/><path d="M0.5 6 H11.5 M6 0.5 Q3 6 6 11.5 M6 0.5 Q9 6 6 11.5" fill="none" stroke="var(--earth)" stroke-width="0.8"/></svg>
        www.meadowlarkreview.com
      </li>
    </ul>
  </section>

  <section class="card card--back" aria-label="Card back">
    <div class="back-name">
      <span class="back-name__square"></span>
      <span class="back-name__text">Meadowlark Property Review</span>
    </div>
    <p class="services">
      Residential appraisals &bull; Home inspection<br>
      Pest inspection and radon gas measurement.
    </p>
  </section>

</main>
</body>
</html>
```